Direct Response Coupon/Flyer for Trade Show

We are looking for something simple and quick. Using our logo and maybe some stock photos.
We need a call to action piece with the following
1. " Every $5,000 save $1,000"
2. Limited time offer. Must reserve your procedure by June 15th
3. content is the following : RQHB is a medical tourism company that facilitates wellness by connecting our clients with qualified medical practitioners in Medellin, Colombia offering dental, vision, cosmetic and other medical procedures.
4. full color 3.5x8.25
5. On the bottom near the left or right we need "Member of the Patient Voyage Guild and the attached logo.
6. to speak to a case manger call 888-614-2093
7. our website is rqhb-example.com to get an idea of our brand and style
looking for something quick
We want the same style as the attached brochure
Trade

```html
<!DOCTYPE html>
<html lang="en">
<head>
<meta charset="utf-8">
<title>RQHB – Trade Show Offer Flyer</title>
<link rel="stylesheet" href="https://fonts.googleapis.com/css2?family=Oswald:wght@400;500&family=Roboto+Condensed:wght@400;700&display=swap">
<style>
  :root {
    --teal: #1a9ea6;
    --teal-band: #27a3aa;
    --black: #0b0b0b;
    --white: #ffffff;
    --paper-top: #f4f4f4;
    --backdrop: #e4e5e6;
    --gold: #c9a34e;
    --footer-grey: #cfcfcf;
  }
  * { box-sizing: border-box; margin: 0; padding: 0; }
  html, body { width: 1200px; height: 1200px; overflow: hidden; }
  body {
    background: var(--backdrop);
    font-family: "Roboto Condensed", "Arial Narrow", sans-serif;
    position: relative;
  }
  .flyer {
    position: absolute;
    left: 362px;
    top: 40px;
    width: 476px;
    height: 1120px;
    display: flex;
    flex-direction: column;
    box-shadow: 0 4px 18px rgba(0,0,0,0.18);
  }
  .offer {
    height: 522px;
    background: linear-gradient(180deg, var(--white) 0%, var(--paper-top) 100%);
    position: relative;
    padding: 20px 20px 0;
  }
  .offer-headline {
    font-family: "Oswald", "Arial Narrow", sans-serif;
    font-weight: 500;
    color: var(--teal);
    font-size: 72px;
    line-height: 128px;
    text-align: center;
    white-space: nowrap;
  }
  .offer-headline span { display: block; }
  .offer-deadline {
    margin: 4px 20px 0;
    font-family: "Oswald", "Arial Narrow", sans-serif;
    font-weight: 500;
    color: var(--teal);
    font-size: 23px;
    line-height: 44px;
    letter-spacing: 0.3px;
  }
  .offer-deadline span {
    display: block;
    text-align: justify;
    text-align-last: justify;
    white-space: nowrap;
  }
  .offer-deadline sup { font-size: 12px; line-height: 0; }
  .journey {
    position: absolute;
    left: 0;
    top: 368px;
    width: 476px;
    height: 150px;
  }
  .about {
    height: 233px;
    background: var(--teal-band);
    padding: 30px 48px 0;
  }
  .about-text {
    color: var(--white);
    font-family: "Oswald", "Arial Narrow", sans-serif;
    font-weight: 400;
    font-size: 19.5px;
    line-height: 33px;
  }
  .about-text span {
    display: block;
    white-space: nowrap;
    text-align: justify;
    text-align-last: justify;
  }
  .about-text span.last { text-align-last: left; }
  .brand-footer {
    flex: 1;
    background: var(--black);
    position: relative;
  }
  .brand-name {
    position: absolute;
    left: 96px;
    top: 52px;
    display: flex;
    align-items: center;
    gap: 22px;
  }
  .brand-dot {
    width: 54px; height: 54px;
    border-radius: 50%;
    border: 3px solid var(--teal);
  }
  .brand-word {
    font-size: 50px;
    font-weight: 400;
    color: var(--teal);
    letter-spacing: 3px;
  }
  .membership {
    position: absolute;
    left: 146px;
    top: 172px;
    display: flex;
    align-items: center;
    gap: 20px;
  }
  .membership-text {
    font-family: "Oswald", "Arial Narrow", sans-serif;
    font-weight: 500;
    color: var(--gold);
    font-size: 15px;
    line-height: 22px;
    text-align: right;
    letter-spacing: 0.3px;
  }
  .membership-badge {
    width: 64px; height: 64px;
    border-radius: 50%;
    background: radial-gradient(circle at 40% 35%, #e9cc7c 0%, var(--gold) 55%, #8a6a22 100%);
  }
  .contact {
    position: absolute;
    left: 0; right: 0;
    bottom: 30px;
    text-align: center;
    color: var(--footer-grey);
    font-size: 15px;
    letter-spacing: 0.2px;
  }
  .contact .divider {
    display: inline-block;
    width: 1px; height: 20px;
    background: var(--footer-grey);
    vertical-align: middle;
    margin: 0 10px;
  }
</style>
</head>
<body>
  <main class="flyer">
    <section class="offer">
      <h1 class="offer-headline"><span>Every $5,000</span><span>save $1,000!</span></h1>
      <p class="offer-deadline"><span>Limited time offer. Must reserve</span><span>your procedure by June 15<sup>th</sup>.</span></p>
      <svg class="journey" viewBox="0 0 476 150" width="476" height="150">
        <defs>
          <linearGradient id="sky" x1="0" y1="0" x2="0" y2="1">
            <stop offset="0" stop-color="#8fa5c4"/>
            <stop offset="0.6" stop-color="#c9b4a8"/>
            <stop offset="1" stop-color="#4e5a78"/>
          </linearGradient>
          <linearGradient id="lagoon" x1="0" y1="0" x2="0" y2="1">
            <stop offset="0" stop-color="#9fc9e8"/>
            <stop offset="0.45" stop-color="#6b8f7a"/>
            <stop offset="1" stop-color="#2fbcb8"/>
          </linearGradient>
          <linearGradient id="clinic" x1="0" y1="0" x2="1" y2="1">
            <stop offset="0" stop-color="#eef1f0"/>
            <stop offset="1" stop-color="#a9b3b4"/>
          </linearGradient>
        </defs>
        <line x1="88" y1="72" x2="388" y2="72" stroke="var(--teal)" stroke-width="5"/>
        <circle cx="88" cy="72" r="66" fill="url(#sky)" stroke="var(--teal)" stroke-width="6" role="img" aria-label="Photo of a passenger jet taking off at dusk"/>
        <circle cx="238" cy="72" r="66" fill="url(#lagoon)" stroke="var(--teal)" stroke-width="6" role="img" aria-label="Photo of overwater bungalows on a turquoise lagoon"/>
        <circle cx="388" cy="72" r="66" fill="url(#clinic)" stroke="var(--teal)" stroke-width="6" role="img" aria-label="Photo of a bright modern dental treatment room"/>
      </svg>
    </section>

    <section class="about">
      <p class="about-text">
        <span>RQHB is a medical tourism company that</span>
        <span>facilitates wellness by connecting our</span>
        <span>clients with qualified medical practitioners</span>
        <span>in Medellin, Colombia offering dental, vision,</span>
        <span class="last">cosmetic and other medical procedures.</span>
      </p>
    </section>

    <footer class="brand-footer">
      <div class="brand-name">
        <span class="brand-dot"></span>
        <span class="brand-word">RQHB</span>
      </div>
      <div class="membership">
        <p class="membership-text">MEMBER OF THE<br>PATIENT VOYAGE GUILD</p>
        <span class="membership-badge" role="img" aria-label="Membership seal"></span>
      </div>
      <p class="contact">rqhb-example.com<span class="divider"></span>to speak to a case manger call 888-614-2093</p>
    </footer>
  </main>
</body>
</html>
```